Need a website where people can find information about the newly formed Northmere Valuation Oversight Board. Soon after, we will need a place to publish our findings as we audit each municipality in the State of Wisconsin. I have a logo (designed by Artwell Hub), a MS Word document showing the content and a set of images to choose from that we can purchase from Pixmarla.com (found here https://www.pixmarla.com/collaboration/boards/-Xq7TbLwRmNoPzYkAuH-Jd)

```html
<!DOCTYPE html>
<html lang="en">
<head>
<meta charset="utf-8">
<title>Northmere Valuation Oversight Board</title>
<link href="https://fonts.googleapis.com/css2?family=Montserrat:wght@600;700;800&family=Roboto:wght@400;500;700&display=swap" rel="stylesheet">
<style>
:root{
  --green:#3f7d1b;
  --green-dark:#2f6412;
  --green-soft:#4d8a27;
  --ink:#111111;
  --body:#555555;
  --white:#ffffff;
  --line:#e3e3e3;
}
*{box-sizing:border-box;margin:0;padding:0}
html,body{width:1200px;height:4065px;overflow:hidden}
body{position:relative;font-family:'Roboto',sans-serif;color:var(--body);background:var(--white)}
.abs{position:absolute}
.heading{font-family:'Montserrat',sans-serif;font-weight:800;color:var(--ink);letter-spacing:-0.5px;line-height:1.15}
.btn{position:absolute;display:flex;align-items:center;justify-content:center;gap:8px;border-radius:30px;background:var(--green);color:var(--white);font-family:'Roboto',sans-serif;font-weight:700;font-size:14px;text-transform:uppercase}
.btn .dot{width:13px;height:13px;border-radius:50%;background:var(--white);position:relative}
.btn .dot::after{content:"";position:absolute;left:4px;top:3px;border-left:6px solid var(--green);border-top:3.5px solid transparent;border-bottom:3.5px solid transparent}
.placeholder{position:absolute}

/* header + hero */
.hero{position:absolute;left:0;top:0;width:1200px;height:647px;background:linear-gradient(160deg,#d9dccf 0%,#c6cbb8 40%,#b9c0a8 70%,#cfd3c4 100%)}
.hero-veil{position:absolute;inset:0;background:linear-gradient(90deg,rgba(255,255,255,.55),rgba(255,255,255,.2))}
.brand{position:absolute;left:110px;top:14px;width:104px;height:104px;border-radius:50%;background:var(--green);color:var(--white);font-family:'Montserrat',sans-serif;font-weight:800;font-size:24px;display:flex;align-items:center;justify-content:center}
.nav{position:absolute;left:237px;top:85px;display:flex;gap:15px;font-size:11px;font-weight:500;color:var(--ink)}
.contact-mail{position:absolute;left:723px;top:20px;display:flex;gap:14px;align-items:center}
.mail-box{width:36px;height:36px;background:var(--green);border-radius:3px;display:flex;align-items:center;justify-content:center}
.contact-mail small{display:block;font-size:11px;color:#333}
.contact-mail b{font-size:14px;color:var(--ink);font-weight:500}
.donate{left:947px;top:20px;width:140px;height:38px;text-transform:none;font-weight:500;font-size:15px}
.hero-title{left:112px;top:250px;font-size:37px;width:520px}
.hero-sub{left:112px;top:358px;font-size:16px;color:#222;line-height:1.6;width:460px}
.hero-btn{left:112px;top:436px;width:208px;height:50px;font-size:16px}
.hero-mark{left:660px;top:150px;width:460px;height:500px}
.arrow{position:absolute;top:316px;width:40px;height:40px;border-radius:50%;background:#222;display:flex;align-items:center;justify-content:center}
.dots{position:absolute;left:553px;top:595px;display:flex;gap:6px}
.dots span{width:18px;height:4px;background:#999;border-radius:2px}
.dots span.on{background:var(--green)}

/* who we are */
.who-img{left:112px;top:750px;width:458px;height:401px;border:3px solid #fff;box-shadow:0 4px 14px rgba(0,0,0,.25);background:linear-gradient(135deg,#8fb0b8 0%,#d9c6a1 45%,#c99a55 70%,#b3b3a8 100%)}
.dot-grid{left:70px;top:1005px;width:250px;height:190px;background-image:radial-gradient(#c9c9c9 1.6px,transparent 1.8px);background-size:12px 12px}
.who-title{left:646px;top:752px;font-size:35px}
.who-text{left:646px;top:832px;width:442px;font-size:13.5px;line-height:24.5px;text-align:justify}
.who-text p+p{margin-top:14px}
.who-btn{left:646px;top:1097px;width:172px;height:41px;font-size:13.5px}

/* recommendations */
.recs{left:0;top:1255px;width:1200px;height:643px;background:linear-gradient(180deg,var(--green) 0%,var(--green-soft) 55%,#3b7618 100%)}
.recs-title{left:0;top:1328px;width:1200px;text-align:center;color:var(--white);font-size:38px}
.rec-label{position:absolute;color:var(--white);font-weight:700;font-size:18px;line-height:1.4}
.rec-svg{left:0;top:1255px}

/* uniform */
.uni-title{left:112px;top:1955px;font-size:35px}
.rule{position:absolute;height:4px;width:70px;background:var(--green)}
.uni-text{left:112px;top:2080px;width:432px;font-size:13.5px;line-height:24px;text-align:justify}
.uni-text p+p{margin-top:9px}
.uni-btn{left:112px;top:2308px;width:171px;height:45px;font-size:13.5px}
.uni-img{left:600px;top:1898px;width:600px;height:505px;background:linear-gradient(135deg,#2a2a2a 0%,#5a5d62 35%,#d8dadd 60%,#f1f1f1 100%)}

/* blog */
.blog-title{left:0;top:2493px;width:1200px;text-align:center;font-size:38px}
.card{position:absolute;top:2585px;width:310px;height:387px;background:#fff;border-radius:8px;box-shadow:0 2px 14px rgba(0,0,0,.14);text-align:center}
.card .thumb{position:absolute;left:7px;top:6px;width:296px;height:204px}
.card .date{position:absolute;top:233px;width:100%;font-size:13px;color:#777}
.card h3{position:absolute;top:256px;width:100%;font-size:16px;font-weight:700;color:var(--ink)}
.card p{position:absolute;top:293px;left:20px;right:20px;font-size:13.5px;line-height:22px}
.card .more{position:absolute;top:349px;width:100%;font-size:14px;font-weight:700;color:var(--green);display:flex;justify-content:center;gap:7px;align-items:center}
.card .more .dot{width:13px;height:13px;background:var(--green);border-radius:50%;position:relative}
.card .more .dot::after{content:"";position:absolute;left:4px;top:3px;border-left:6px solid #fff;border-top:3.5px solid transparent;border-bottom:3.5px solid transparent}

/* contact */
.contact{left:0;top:3063px;width:1200px;height:624px;background:linear-gradient(180deg,#3c7a19 0%,#4a8827 50%,#3a7518 100%)}
.contact-title{left:0;top:3103px;width:1200px;text-align:center;color:var(--white);font-size:38px}
.field-label{position:absolute;color:var(--white);font-weight:700;font-size:15px}
.field{position:absolute;background:#fff;border-radius:4px;font-size:11px;color:#aaa;padding:18px 20px 0}
.send{left:499px;top:3576px;width:204px;height:49px;background:#fff;color:var(--green);font-size:16px;font-weight:700}

/* footer */
.foot-brand{left:126px;top:3752px;width:186px;height:186px;border-radius:50%;background:var(--green);color:#fff;font-family:'Montserrat',sans-serif;font-weight:800;font-size:38px;display:flex;align-items:center;justify-content:center}
.foot-col{position:absolute;top:3757px;font-size:13.5px;color:#555}
.foot-col h4{font-size:16px;color:var(--ink);font-weight:700;margin-bottom:24px}
.foot-col li{list-style:none;height:27.6px}
.foot-contact{left:875px;top:3757px;width:230px}
.foot-contact h4{font-size:16px;color:var(--ink);font-weight:700;margin-bottom:22px}
.ci{position:relative;padding-left:23px;font-size:13px;line-height:18px;margin-bottom:14px}
.ci b{display:block;font-size:11px;color:var(--ink)}
.ci svg{position:absolute;left:0;top:2px}
.foot-rule{left:112px;top:3997px;width:976px;height:1px;background:var(--line)}
.socials{left:112px;top:4016px;display:flex;gap:9px}
.socials span{width:28px;height:28px;border-radius:50%;border:1.5px solid #444}
.copy{left:0;top:4023px;width:1200px;text-align:center;font-size:14px;color:#444}
.chat{left:1106px;top:3958px;width:36px;height:36px;border-radius:50%;background:var(--green);display:flex;align-items:center;justify-content:center}
</style>
</head>
<body>

<section class="hero" aria-label="Introduction">
  <div class="placeholder" style="inset:0" role="img" aria-label="Aerial photo of a suburban neighbourhood with houses and autumn trees"></div>
  <div class="hero-veil"></div>
</section>

<header>
  <div class="brand abs">NVOB</div>
  <div class="contact-mail">
    <div class="mail-box"><svg width="20" height="14" viewBox="0 0 20 14"><rect x="1" y="1" width="18" height="12" fill="none" stroke="#fff" stroke-width="1.6"/><path d="M1 1l9 7 9-7" fill="none" stroke="#fff" stroke-width="1.6"/></svg></div>
    <div><small>Email Address</small><b>mhalden@nvob.pro</b></div>
  </div>
  <div class="btn donate">Donate Now</div>
  <nav class="nav">
    <span>Who We Are</span><span>Property Tax Problem</span><span>What is Uniform Taxation?</span><span>Blog</span><span>Audits</span><span>NVOB Recommendations</span><span>Meet the Volunteers</span><span>Corrections</span><span>Contact</span>
  </nav>
</header>

<h1 class="heading abs hero-title">NORTHMERE VALUATION OVERSIGHT BOARD</h1>
<p class="abs hero-sub">The Northmere Valuation Oversight Board (NVOB) is a non-partisan, not-for-profit, watchdog</p>
<div class="btn hero-btn">Get Started <span class="dot"></span></div>
<svg class="abs hero-mark" viewBox="0 0 460 500" role="img" aria-label="Board emblem">
  <circle cx="250" cy="250" r="230" fill="#3f7d1b"/>
  <text x="250" y="275" text-anchor="middle" font-family="Montserrat, sans-serif" font-weight="800" font-size="88" fill="#fff">NVOB</text>
</svg>
<div class="arrow" style="left:27px"><svg width="12" height="16"><path d="M9 2L3 8l6 6" fill="none" stroke="#fff" stroke-width="2"/></svg></div>
<div class="arrow" style="left:1123px"><svg width="12" height="16"><path d="M3 2l6 6-6 6" fill="none" stroke="#fff" stroke-width="2"/></svg></div>
<div class="dots"><span class="on"></span><span></span><span></span><span></span></div>

<section aria-label="Who we are">
  <div class="abs dot-grid"></div>
  <div class="placeholder who-img" role="img" aria-label="Collage of a lone tree in a field beside a pinned property tax note on a site plan"></div>
  <h2 class="heading abs who-title">WHO WE ARE</h2>
  <div class="abs who-text">
    <p>The Northmere Valuation Oversight Board (NVOB) is a non-partisan, not-for-profit, watchdog organization with a mission to ensure uniform property taxation statewide. It was started in February of 2022 as the Northmere Valuation Oversight Board, LLC and does business as the Northmere Valuation Oversight Board.</p>
    <p>The Northmere Valuation Oversight Board audits local municipal governments who are responsible for producing a uniform property tax assessment roll each year.</p>
  </div>
  <div class="btn who-btn">Read More <span class="dot"></span></div>
</section>

<section aria-label="NVOB recommendations">
  <div class="abs recs" role="img" aria-label="Green-tinted photo of farm fields"></div>
  <h2 class="heading abs recs-title">NVOB RECOMMENDATIONS</h2>
  <svg class="abs rec-svg" width="1200" height="643" viewBox="0 1255 1200 643">
    <g fill="none" stroke="rgba(255,255,255,.55)" stroke-width="1.3">
      <path d="M449 1453h60l40 45"/><path d="M743 1453h-60l-40 45"/>
      <path d="M449 1647h60l40-40"/><path d="M743 1647h-60l-40-40"/>
      <path d="M600 1643v49"/>
    </g>
    <circle cx="600" cy="1551" r="92" fill="#3f7d1b" stroke="#fff" stroke-width="5"/>
    <circle cx="600" cy="1551" r="78" fill="#fff"/>
    <text x="600" y="1562" text-anchor="middle" font-family="Montserrat, sans-serif" font-weight="800" font-size="30" fill="#3f7d1b">NVOB</text>
    <g fill="#3f7d1b" stroke="#fff" stroke-width="5">
      <circle cx="409" cy="1453" r="38"/><circle cx="783" cy="1453" r="38"/>
      <circle cx="409" cy="1647" r="38"/><circle cx="783" cy="1647" r="38"/>
      <circle cx="600" cy="1732" r="38"/>
    </g>
    <g fill="#fff"><circle cx="409" cy="1453" r="31"/><circle cx="783" cy="1453" r="31"/><circle cx="409" cy="1647" r="31"/><circle cx="783" cy="1647" r="31"/><circle cx="600" cy="1732" r="31"/></g>
    <g fill="none" stroke="#3f7d1b" stroke-width="2">
      <path d="M395 1468h28M397 1446l12-9 12 9zM399 1450v15M405 1450v15M413 1450v15M419 1450v15"/>
      <path d="M774 1448q9-6 18 0l4 18h-26zM778 1442h10"/><text x="783" y="1463" text-anchor="middle" font-size="10" fill="#3f7d1b" stroke="none" font-family="Roboto, sans-serif">$</text>
      <rect x="396" y="1636" width="26" height="18" rx="2"/><circle cx="403" cy="1644" r="3"/><circle cx="415" cy="1644" r="3"/><path d="M405 1654v8h8v-8"/>
      <rect x="772" y="1633" width="18" height="26"/><path d="M776 1640h10M776 1646h10M776 1652h6M790 1650l6 6"/>
      <rect x="589" y="1718" width="22" height="28"/><path d="M593 1726h14M593 1733h8M601 1741l6-6"/>
    </g>
  </svg>
  <div class="rec-label" style="left:192px;top:1440px">For Municipalities</div>
  <div class="rec-label" style="left:852px;top:1428px">For the Department<br>of Revenue</div>
  <div class="rec-label" style="left:164px;top:1634px">For Boards of Review</div>
  <div class="rec-label" style="left:852px;top:1634px">For Legislators</div>
  <div class="rec-label" style="left:540px;top:1788px">For Taxpayers</div>
</section>

<section aria-label="What is uniform taxation">
  <h2 class="heading abs uni-title">WHAT IS UNIFORM<br>TAXATION?</h2>
  <div class="rule" style="left:112px;top:2048px"></div>
  <div class="abs uni-text">
    <p>Uniform taxation means similar properties have similar values for taxation purposes.</p>
    <p>For example, if you own a condominium assessed for tax purposes at $200,000 and your neighbor has the same unit but is assessed at $160,000, your values, and therefore your taxes, will be significantly different. You will be paying more of the tax burden than your neighbor, even though the market value of both units is the same. This is non-uniform taxation.</p>
  </div>
  <div class="btn uni-btn">Read More <span class="dot"></span></div>
  <div class="placeholder uni-img" role="img" aria-label="Hand holding a pen over a printed spreadsheet beside a laptop keyboard"></div>
</section>

<section aria-label="Our blog">
  <h2 class="heading abs blog-title">OUR BLOG</h2>
  <div class="rule" style="left:565px;top:2544px"></div>
  <article class="card" style="left:110px">
    <div class="placeholder thumb" role="img" aria-label="Stone city hall building lettering" style="background:linear-gradient(120deg,#c9b89c,#8f7c63 60%,#6f88a8)"></div>
    <div class="date">&#9635; February 2, 2022</div>
    <h3>Lorem dolor amet, consectetur</h3>
    <p>Sed ut perspiciatis unde omnis iste natus error sit voluptatem accusantium</p>
    <div class="more">READ MORE <span class="dot"></span></div>
  </article>
  <article class="card" style="left:444px">
    <div class="placeholder thumb" role="img" aria-label="Finger pressing one pan of a balance scale" style="background:linear-gradient(120deg,#d7d7d7,#a7a7a7 55%,#e9e9e9)"></div>
    <div class="date">&#9635; February 2, 2022</div>
    <h3>Lorem dolor amet, consectetur</h3>
    <p>Sed ut perspiciatis unde omnis iste natus error sit voluptatem accusantium</p>
    <div class="more">READ MORE <span class="dot"></span></div>
  </article>
  <article class="card" style="left:777px">
    <div class="placeholder thumb" role="img" aria-label="Metal gears labelled with audit and review words" style="background:linear-gradient(120deg,#5a5a5a,#9a9a9a 50%,#444)"></div>
    <div class="date">&#9635; February 2, 2022</div>
    <h3>Lorem dolor amet, consectetur</h3>
    <p>Sed ut perspiciatis unde omnis iste natus error sit voluptatem accusantium</p>
    <div class="more">READ MORE <span class="dot"></span></div>
  </article>
</section>

<section aria-label="Contact us">
  <div class="abs contact" role="img" aria-label="Green-tinted photo of a city skyline by the water"></div>
  <h2 class="heading abs contact-title">CONTACT US</h2>
  <div class="rule" style="left:565px;top:3154px;background:#fff"></div>
  <div class="field-label" style="left:147px;top:3195px">First Name</div>
  <div class="field" style="left:147px;top:3221px;width:439px;height:49px">Your First Name</div>
  <div class="field-label" style="left:613px;top:3195px">Last Name</div>
  <div class="field" style="left:613px;top:3221px;width:439px;height:49px">Your Last Name</div>
  <div class="field-label" style="left:147px;top:3296px">Email Address</div>
  <div class="field" style="left:147px;top:3322px;width:439px;height:49px">Your Email Address</div>
  <div class="field-label" style="left:613px;top:3296px">Subject</div>
  <div class="field" style="left:613px;top:3322px;width:439px;height:49px">Your Subject</div>
  <div class="field-label" style="left:147px;top:3394px">Message</div>
  <div class="field" style="left:147px;top:3420px;width:905px;height:112px">Enter Your Message</div>
  <div class="btn send">SEND MESSAGE</div>
</section>

<footer>
  <div class="abs foot-brand">NVOB</div>
  <div class="foot-col" style="left:425px">
    <h4>Quick Links</h4>
    <ul><li>Who We Are</li><li>Property Tax Problem</li><li>What is Uniform Taxation?</li><li>Blog</li><li>Audits</li><li>NVOB Recommendations</li></ul>
  </div>
  <div class="foot-col" style="left:679px">
    <h4>About Company</h4>
    <ul><li>Privacy Policy</li><li>Terms of Service</li><li>Site Map</li><li>Imprint</li><li>Terms And Conditions</li></ul>
  </div>
  <div class="abs foot-contact">
    <h4>Contact Us</h4>
    <div class="ci"><svg width="13" height="13" viewBox="0 0 13 13"><path d="M2 1l3 0 1 3-2 1q1 3 4 4l1-2 3 1v3q-7 1-10-10z" fill="#3f7d1b"/></svg><b>Phone</b>+1 (888) 888-8888</div>
    <div class="ci"><svg width="14" height="11" viewBox="0 0 14 11"><rect width="14" height="11" fill="#3f7d1b"/><path d="M1 1l6 5 6-5" fill="none" stroke="#fff"/></svg><b>Email</b>mhalden@nvob.pro</div>
    <div class="ci"><svg width="11" height="15" viewBox="0 0 11 15"><path d="M5.5 15S0 8 0 5.5a5.5 5.5 0 0111 0C11 8 5.5 15 5.5 15z" fill="#3f7d1b"/><circle cx="5.5" cy="5.5" r="2" fill="#fff"/></svg><b>Location</b>81 Lorem ipsum dolor sit amet, consectetur adipiscing elit,</div>
  </div>
  <div class="abs chat"><svg width="18" height="16" viewBox="0 0 18 16"><path d="M9 1C4.6 1 1 3.9 1 7.4c0 2 1.1 3.7 2.9 4.9L3 15l3.5-2c.8.2 1.6.3 2.5.3 4.4 0 8-2.9 8-6.4S13.4 1 9 1z" fill="#fff"/></svg></div>
  <div class="abs foot-rule"></div>
  <div class="abs socials" aria-label="Social links"><span></span><span></span><span></span><span></span></div>
  <div class="abs copy">2022 Copyright - &nbsp;NVOB &nbsp;| All Rights Reserved</div>
</footer>

</body>
</html>
```